Marlo K Dress Designs

My company (MarloK) designs and creates ladies fashion garments. I am a one person company at the moment with plans to bring on additional staff as the workload increases. At this stage I would prefer to focus on developing regional clients around Wellington, New Zealand so I can personalise the service. Expansion beyond the Wellington region is a dream in the future if all goes well with the website and the business.

I love working with people to create fashion garments for them that showcase their personalities and beauty, whatever their body type or physical appearance. I love helping my clients select the best designs, fabrics, colours and styles to look and feel the very best they can appropriate to the occasion they are dressing for. Sometimes its high-end fashion, sometimes its for daily wearing and on the odd occasion its just to be quirky and have fun with fashion. Clients typically want that special garment or outfit for special occasions like balls, weddings, racedays, reunions, concerts, anniversaries, receptions, functions and formal gatherings.

I have created a range of garments (about 12) which I would like to be showcased on the website. I can reproduce those garment showcased for clients, or I could work with the client to create a special one of a kind outfit for them, or reproduce off an existing dress design, or alter an existing outfit. have a customer focussed industry that focussing on bespoke garments rather than trying to compete with low cost mass produced ladies fashion garment.

I would like to have the prospective clients contact me by email directly from the website and work with them to design, quote, produce and tailor what they want. These fashion garments will be more expensive than off-the-rack garments readily available in shops or online. But they will be specifically tailored for the individuals. Clients will be given a quote based upon the design, type and quantity of the material used before I create the garment.

A couple of quotes in regards to my fashion design that expresses my love for creating and producing great garments for people:
- Percy Haldane - 'You can never be overdressed or overeducated.'
- Pipsy - 'There's no need to dress like everybody else. Its much more fun to create your own.'
- Carlo Benvetti- 'I really want to make clothes that are feminine and help women look beautiful.'

I want to have this website hosted on a server and I want to be able to amend and update the photos and other content myself.

I like a mix of old and new sewing related art/images.

My email address and phone number should be in the contact page. They are shown in the cards below. I will upload photos of my creations soon.

Industry/Entity Type

Fashion

Coding

Coded - Design and coding required

Number of Pages Required

3 page

Colors

Designer to choose colors to be used in the design.

Requirements
Must have
• Blog
• Services (Formal Dresses, Alterations, Buisness attire, every day wear, style consults)
Should not have
• Products

```html
<!DOCTYPE html>
<html lang="en">
<head>
<meta charset="utf-8">
<title>Marlo K Dress Designs</title>
<link rel="stylesheet" href="https://fonts.googleapis.com/css2?family=Playfair+Display:wght@400;700&family=Open+Sans:wght@400;600&display=swap">
<style>
:root{
  --wine:#8b1538;
  --olive:#8a9a2e;
  --ink:#1e1e1e;
  --text:#4a4a4a;
  --dark:#222222;
  --footer:#2b2b2b;
  --band:#f0f0f0;
  --quote-bg:#eeeeee;
  --white:#ffffff;
}
*{margin:0;padding:0;box-sizing:border-box}
html,body{width:1200px;height:2432px;overflow:hidden}
body{position:relative;background:var(--white);font-family:"Open Sans",Arial,sans-serif;color:var(--ink)}
.abs{position:absolute}

/* header */
.site-header{left:0;top:0;width:1200px;height:151px;background:var(--white)}
.brand{left:133px;top:22px;font-family:"Playfair Display",Georgia,serif;font-size:72px;line-height:1;color:var(--wine);font-weight:400;white-space:nowrap}
.top-contact-row{right:133px;top:38px;display:flex;gap:30px;white-space:nowrap}
.top-contact{font-size:18px;font-weight:600;display:flex;align-items:center;gap:8px;color:var(--ink)}
.top-contact svg{width:16px;height:16px;fill:var(--ink)}
.main-nav{top:114px;left:0;width:1200px;font-family:"Playfair Display",Georgia,serif;font-size:17px;color:#333}
.main-nav span{position:absolute;white-space:nowrap}
.main-nav .current{color:var(--wine)}

/* hero */
.hero{left:0;top:151px;width:1200px;height:614px;background:linear-gradient(100deg,#3a2c26 0%,#6b5347 18%,#b89a8f 32%,#d9b6b0 40%,#7a6258 55%,#4b3a34 75%,#3a2e2b 100%)}
.hero-quote{left:692px;top:388px;width:375px;height:141px;background:rgba(255,255,255,.93);text-align:right;padding:16px 22px 0 0;font-family:"Playfair Display",Georgia,serif;font-size:24px;line-height:32px;color:#333;white-space:nowrap}
.hero-quote .by{color:var(--olive);margin-top:6px}
.hero-arrow{top:445px;width:28px;height:28px;background:rgba(0,0,0,.55);display:flex;align-items:center;justify-content:center}
.hero-arrow svg{width:16px;height:16px;fill:var(--white)}

/* feature rows */
.section-title{font-family:"Playfair Display",Georgia,serif;font-size:42px;font-weight:400;line-height:1.1;white-space:nowrap}
.section-lead{font-size:19px;line-height:1.4}
.section-body{font-size:12px;line-height:20.7px}
.btn{display:flex;align-items:center;justify-content:center;width:104px;height:43px;font-family:"Playfair Display",Georgia,serif;font-size:15px}

.welcome{left:0;top:767px;width:1200px;height:462px}
.welcome .section-title{position:absolute;left:133px;top:68px;color:var(--wine)}
.welcome .section-lead{position:absolute;left:133px;top:134px;width:465px;color:var(--ink)}
.welcome .section-body{position:absolute;left:133px;top:200px;width:460px;color:var(--text)}
.welcome .btn{position:absolute;left:133px;top:341px;border:1px solid #999;color:#555}
.welcome .photo{position:absolute;left:634px;top:78px;width:433px;height:306px;background:linear-gradient(135deg,#e9ebef 0%,#d9dce3 40%,#9fb6d6 62%,#eef0f3 100%)}

.craft{left:0;top:1229px;width:1200px;height:472px;background:var(--dark)}
.craft .photo{position:absolute;left:133px;top:81px;width:431px;height:310px;background:linear-gradient(160deg,#f2efec 0%,#e2d6cc 45%,#d4b49a 75%,#c9a488 100%)}
.craft .section-title{position:absolute;left:602px;top:72px;color:var(--white)}
.craft .section-lead{position:absolute;left:602px;top:138px;width:465px;color:var(--white)}
.craft .section-body{position:absolute;left:602px;top:204px;width:460px;color:#8f8f8f}
.craft .btn{position:absolute;left:601px;top:344px;border:1px solid #999;color:#bbb}

/* reviews */
.reviews{left:0;top:1701px;width:1200px;height:514px}
.reviews .section-title{position:absolute;left:0;width:1200px;top:68px;text-align:center;color:var(--wine)}
.review-card{position:absolute;left:133px;top:144px;width:934px;height:210px;background:var(--quote-bg);text-align:center;padding:30px 60px 0;font-family:"Playfair Display",Georgia,serif;font-size:25px;line-height:1.42;color:#333}
.avatar{position:absolute;left:552px;top:304px;width:96px;height:96px;border-radius:50%;border:3px solid var(--white);background:radial-gradient(circle at 50% 45%,#e8c9ae 0%,#caa17c 55%,#8a6a4e 100%)}
.reviewer{position:absolute;left:0;width:1200px;top:412px;text-align:center;font-family:"Playfair Display",Georgia,serif;font-size:16px;color:var(--olive)}
.review-arrow{position:absolute;top:234px;width:24px;height:30px}
.review-arrow path{fill:none;stroke:#999;stroke-width:2.5}

/* contact band */
.contact-band{left:0;top:2215px;width:1200px;height:101px;background:var(--band);display:flex;align-items:center;justify-content:center;gap:22px;font-size:17px;color:var(--ink);white-space:nowrap}
.contact-band svg{width:14px;height:14px;fill:var(--ink);margin-right:6px;vertical-align:-1px}

/* footer */
.site-footer{left:0;top:2316px;width:1200px;height:116px;background:var(--footer)}
.footer-nav{position:absolute;left:133px;top:41px;font-size:12px;color:#bbb;word-spacing:2px}
.copyright{position:absolute;left:133px;top:70px;font-size:12px;color:#aaa}
.social{position:absolute;top:55px;width:16px;height:16px;border-radius:50%;background:#aaa}
</style>
</head>
<body>

<header class="abs site-header">
  <div class="abs brand">Marlo K</div>
  <div class="abs top-contact-row">
    <div class="top-contact">
      <svg viewBox="0 0 16 16"><path d="M1 3h14v10H1z M1 3l7 6 7-6" fill="none" stroke="#1e1e1e" stroke-width="1.6"/></svg>
      marlokdesigns@mailbox.co.nz
    </div>
    <div class="top-contact">
      <svg viewBox="0 0 16 16"><path d="M3 1h3l1.5 4-2 1.3a9 9 0 0 0 4.2 4.2L11 8.5l4 1.5v3a2 2 0 0 1-2 2C7 15 1 9 1 3a2 2 0 0 1 2-2z"/></svg>
      021 555 0148
    </div>
  </div>
  <nav class="abs main-nav">
    <span class="current" style="left:535px">Home</span>
    <span style="left:618px">Services</span>
    <span style="left:717px">Reviews</span>
    <span style="left:814px">Blog</span>
    <span style="left:885px">About Us</span>
    <span style="left:989px">Contact Us</span>
  </nav>
</header>

<section class="abs hero" role="img" aria-label="Fashion photo of a woman in a pink coat and sunglasses against a brick wall"></section>
<blockquote class="abs hero-quote">
  “ You can never be overdressed<br>or overeducated „
  <div class="by">- Percy Haldane</div>
</blockquote>
<div class="abs hero-arrow" style="left:0"><svg viewBox="0 0 16 16"><path d="M7 2 1 8l6 6V10h8V6H7z"/></svg></div>
<div class="abs hero-arrow" style="left:1172px"><svg viewBox="0 0 16 16"><path d="M9 2l6 6-6 6V10H1V6h8z"/></svg></div>

<section class="abs welcome">
  <h1 class="section-title">Welcome to Marlo K</h1>
  <p class="section-lead">Vestibulum condimentum, risus ut posuere cursus, velit justo accumsan sem.</p>
  <p class="section-body">Phasellus consequat sagittis nisi suscipit feugiat. Cras eget leo sed nunc hendrerit ultricies eu at nisl. Praesent iaculis faucibus urna sit amet lacinia. Maecenas consequat justo enim, ac mattis massa imperdiet quis. Fusce eget neque elit. Sed augue orci, elementum in magna congue, tincidunt vulputate erat. Aliquam consectetur orci molestie dictum molestie. Proin eget congue nulla, vel tempor diam. Ut non ante est.</p>
  <a class="btn">Read More</a>
  <div class="photo" role="img" aria-label="Hands sewing patterned fabric beside a sewing machine and thread spools"></div>
</section>

<section class="abs craft">
  <div class="photo" role="img" aria-label="Hands cutting fabric with tailoring scissors on a worktable"></div>
  <h2 class="section-title">Aliquam erat</h2>
  <p class="section-lead">Pellentesque convallis molestie enim amet efficitur lectus sit amet mi pulvinar maximus</p>
  <p class="section-body">Phasellus consequat sagittis nisi suscipit feugiat. Cras eget leo sed nunc hendrerit ultricies eu at nisl. Praesent iaculis faucibus urna sit amet lacinia. Maecenas consequat justo enim, ac mattis massa imperdiet quis. Fusce eget neque elit. Sed augue orci, elementum in magna congue, tincidunt vulputate erat. Aliquam consectetur orci molestie dictum molestie. Proin eget congue nulla, vel tempor diam. Ut non ante est.</p>
  <a class="btn">Read More</a>
</section>

<section class="abs reviews">
  <h2 class="section-title">Reviews</h2>
  <svg class="review-arrow" style="left:43px" viewBox="0 0 24 30"><path d="M18 3 6 15l12 12"/></svg>
  <svg class="review-arrow" style="left:1133px" viewBox="0 0 24 30"><path d="M6 3l12 12L6 27"/></svg>
  <blockquote class="review-card">“ Maecenas vel tortor accumsan quam varius imperdiet vel eget elit. Aenean facilisis tincidunt lectus, id dictum nisi luctus eget. Vivamus efficitur ex condimentum, malesuada eros eget, feugiat nibh „</blockquote>
  <div class="avatar" role="img" aria-label="Portrait photo of the reviewer"></div>
  <div class="reviewer">Emily, City</div>
</section>

<section class="abs contact-band">
  <span><svg viewBox="0 0 16 16"><path d="M8 0a5.5 5.5 0 0 0-5.5 5.5C2.5 10 8 16 8 16s5.5-6 5.5-10.5A5.5 5.5 0 0 0 8 0zm0 8a2.5 2.5 0 1 1 0-5 2.5 2.5 0 0 1 0 5z"/></svg>24 Building name, Street name, City Zipcode</span>
  <span>|</span>
  <span><svg viewBox="0 0 16 16"><path d="M3 1h3l1.5 4-2 1.3a9 9 0 0 0 4.2 4.2L11 8.5l4 1.5v3a2 2 0 0 1-2 2C7 15 1 9 1 3a2 2 0 0 1 2-2z"/></svg>Phone : 021 555 0148</span>
  <span>|</span>
  <span><svg viewBox="0 0 16 16"><path d="M1 3h14v10H1z M1 3l7 6 7-6" fill="none" stroke="#1e1e1e" stroke-width="1.6"/></svg>Email : marlokdesigns@mailbox.co.nz</span>
</section>

<footer class="abs site-footer">
  <div class="footer-nav">Home &nbsp;|&nbsp; Our Garments &nbsp;|&nbsp; Reviews &nbsp;|&nbsp; Blog &nbsp;|&nbsp; About Us &nbsp;|&nbsp; Contact Us</div>
  <div class="copyright">Copyright © 2018 Marlo K. All rights reserved.</div>
  <span class="social" style="left:977px" aria-label="Social link"></span>
  <span class="social" style="left:1011px" aria-label="Social link"></span>
  <span class="social" style="left:1051px" aria-label="Social link"></span>
</footer>

</body>
</html>
```